Kistenhalle
Zielgruppe
Kistenhalle.de vermietet Lagercontainern an Privatkunden und Gewerbetriebende
Vermietung von Stellfächen für Wohnmobile/Boote etc
Das ganze auf einem Gewerbegelände in Köln (Brauweiler)
Aufgabenstellung
Erstellung eines 2-Seitigen DIN lang (10,5 x 21 cm) Flyers
Seite A: Vermietung von Lagercontainern
Seite B: Stellfächen für Wohnmobile/Boote
Wichtig: Die Sicherheit (Zutrittskontrolle, Videoüberwachung, Brandmeldeanlage)
Preise sollen auf Flyern erscheinen, diese wie auch die Textee möchte ich jedoch ändern können.
Alle Texte können auch von der Seite kistenhalle.de übernommen werden
Das Logo (siehe hallen_quartier.ai) müsste noch bearbeitet werden .... also "hallenquartier" raus und dafür "Lagerraum Container" rein
Gerne mit Symbolen arbeiten ..

```html
<!DOCTYPE html>
<html lang="de">
<head>
<meta charset="utf-8">
<title>Kistenhalle – Flyer Seite A und B</title>
<link href="https://fonts.googleapis.com/css2?family=Oswald:wght@500&family=Source+Sans+3:wght@400;600&display=swap" rel="stylesheet">
<style>
  :root{
    --header:#262628;
    --ink:#1f2123;
    --green:#0c7a34;
    --green-soft:#5f9a56;
    --green-panel:#eff5e8;
    --green-line:#86b07c;
    --blue:#1b5da6;
    --text-grey:#7a7a7a;
    --paper:#ffffff;
  }
  *{box-sizing:border-box;margin:0;padding:0}
  html,body{width:1200px;height:1010px;overflow:hidden;background:var(--paper)}
  body{position:relative;font-family:"Source Sans 3",sans-serif;color:var(--ink)}

  .flyer-side{position:absolute;left:170px;width:851px;height:425px;background:var(--paper);
    box-shadow:0 3px 8px rgba(0,0,0,.25);overflow:hidden}
  .side-a{top:60px}
  .side-b{top:536px}

  .side-header{position:absolute;left:0;top:0;width:100%;height:97px;background:var(--header)}
  .brand{position:absolute;left:36px;top:18px;height:63px;display:flex;align-items:center;gap:12px}
  .brand-square{width:26px;height:26px;background:var(--green)}
  .brand-name{font-family:"Source Sans 3",sans-serif;font-weight:600;font-size:34px;color:#ffffff;letter-spacing:.5px}
  .web{position:absolute;right:32px;top:12px;font-size:17px;font-weight:600;color:var(--green-soft)}
  .claims{position:absolute;right:38px;top:54px;display:flex;gap:18px;color:#fff;font-size:25px;font-weight:400}
  .claims li{list-style:none;display:flex;align-items:center;gap:7px}
  .claims svg{width:21px;height:21px}

  .headline{position:absolute;left:32px;top:108px;font-family:"Oswald",sans-serif;font-weight:500;
    font-size:27px;letter-spacing:.2px;color:var(--ink);white-space:nowrap}
  .side-a .headline{transform:scaleX(.88);transform-origin:left center}

  .product-stage{position:absolute;left:0;top:158px;width:100%;height:160px;
    background:linear-gradient(#ffffff 0%,#f1f1f3 60%,#e6e6ea 100%)}
  .visual{position:absolute}
  .visual-container{left:32px;top:166px;width:182px;height:147px;
    background:linear-gradient(90deg,#1d3f8f 0%,#2a54a8 45%,#8a6a40 60%,#c9cdd3 75%,#e1e3e6 100%)}
  .visual-camper{left:430px;top:168px;width:192px;height:143px;border-radius:40px 30px 20px 20px;
    background:linear-gradient(#d9dce1 0%,#f5f6f7 45%,#e4e7ec 80%,#a9adb4 100%)}

  .price-box{position:absolute;top:171px;width:177px;height:136px;border-radius:3px;color:#fff;
    padding:10px 12px 0 13px;border:2px solid #fff;outline:2px solid var(--box)}
  .price-box.green{left:232px;background:var(--green);--box:var(--green)}
  .price-box.blue{left:641px;background:var(--blue);--box:var(--blue)}
  .price{font-size:17px;font-weight:600;line-height:1.2}
  .price small{font-size:14px;font-weight:600}
  .offer{margin-top:10px;font-size:12.3px;font-weight:600;line-height:19px}
  .fine{margin-top:7px;font-size:7.4px;line-height:11.5px;text-align:center}

  .security-bar{position:absolute;left:32px;top:333px;width:785px;height:48px;border:2px solid var(--green-line);
    border-radius:3px;display:flex;align-items:center;justify-content:space-between;padding:0 12px;
    color:var(--green-soft);font-size:15px;font-weight:600}
  .security-bar li{list-style:none;display:flex;align-items:center;gap:3px;white-space:nowrap}
  .security-bar svg{width:13px;height:13px;fill:var(--green-soft)}

  .imprint{position:absolute;left:32px;top:395px;width:787px;display:flex;justify-content:space-between;
    align-items:center;font-size:13px;font-weight:600;color:var(--ink);white-space:nowrap}
  .imprint .dot{font-size:9px}
  .imprint svg{width:10px;height:10px;fill:var(--ink);margin-right:2px;vertical-align:-1px}

  .benefits{position:absolute;left:32px;top:158px;width:785px;height:223px;background:var(--green-panel);
    border:2px solid var(--green-line);border-radius:3px}
  .benefit{position:absolute;top:18px}
  .benefit:nth-child(1){left:15px;width:230px}
  .benefit:nth-child(2){left:274px;width:230px}
  .benefit:nth-child(3){left:537px;width:230px}
  .benefit h3{display:flex;align-items:center;gap:11px;font-size:26px;font-weight:400;color:var(--green-soft)}
  .benefit h3 svg{width:27px;height:27px}
  .benefit p{margin-top:10px;padding-left:5px;font-size:13.5px;line-height:23px;color:var(--text-grey)}
  .benefit:nth-child(2) p,.benefit:nth-child(3) p{padding-left:0}
</style>
</head>
<body>

<svg width="0" height="0" style="position:absolute">
  <symbol id="tick-white" viewBox="0 0 24 24"><circle cx="12" cy="12" r="12" fill="#fff"/><path d="M6.5 12.5l3.7 3.7 7.3-8" stroke="#262628" stroke-width="3" fill="none" stroke-linecap="round" stroke-linejoin="round"/></symbol>
  <symbol id="tick-green" viewBox="0 0 24 24"><circle cx="12" cy="12" r="12" fill="#5f9a56"/><path d="M6.5 12.5l3.7 3.7 7.3-8" stroke="#fff" stroke-width="3" fill="none" stroke-linecap="round" stroke-linejoin="round"/></symbol>
</svg>

<!-- Seite A -->
<section class="flyer-side side-a">
  <header class="side-header">
    <div class="brand"><span class="brand-square"></span><span class="brand-name">Kistenhalle</span></div>
    <div class="web">www.kistenhalle.de</div>
    <ul class="claims">
      <li><svg><use href="#tick-white"/></svg>Günstig</li>
      <li><svg><use href="#tick-white"/></svg>Sicher</li>
      <li><svg><use href="#tick-white"/></svg>Lagern</li>
    </ul>
  </header>

  <h1 class="headline">VERMIETUNG VON LAGERCONTAINERN • STELLFLÄCHEN FÜR WOHNMOBILE / BOOTE</h1>

  <div class="product-stage"></div>
  <div class="visual visual-container" role="img" aria-label="Geöffneter blauer Lagercontainer mit Kartons"></div>
  <div class="price-box green">
    <p class="price">148,- € <small>pro Monat *</small></p>
    <p class="offer">1 Monat gratis bei einer<br>Anmietung ab 3 Monaten</p>
    <p class="fine">*Preis gilt pro Monat und Container für private Vermietung, bei gewerblicher Anmietung zzgl. 19% MwSt</p>
  </div>
  <div class="visual visual-camper" role="img" aria-label="Weißes Wohnmobil"></div>
  <div class="price-box blue">
    <p class="price">148,- € <small>pro Monat *</small></p>
    <p class="offer">1 Monat gratis bei einer<br>Anmietung ab 3 Monaten</p>
    <p class="fine">*Preis gilt pro Monat und Container für private Vermietung, bei gewerblicher Anmietung zzgl. 19% MwSt</p>
  </div>

  <ul class="security-bar">
    <li><svg viewBox="0 0 16 16"><rect x="0" y="4" width="10" height="8" rx="1"/><path d="M10 7l6-3v8l-6-3z"/></svg>Videoüberwachung</li>
    <li><svg viewBox="0 0 16 16"><circle cx="8" cy="8" r="6.5" fill="none" stroke="#5f9a56" stroke-width="2"/><circle cx="8" cy="8" r="2.5"/></svg>Zutrittskontrolle</li>
    <li><svg viewBox="0 0 16 16"><rect x="5" y="5" width="6" height="11" rx="1"/><rect x="6.5" y="1" width="3" height="4"/><path d="M9.5 2h4v2h-4z"/></svg>Brandmeldeanlage</li>
    <li><svg viewBox="0 0 16 16"><rect x="2" y="7" width="12" height="9" rx="1"/><path d="M4.5 7V5a3.5 3.5 0 017 0v2" fill="none" stroke="#5f9a56" stroke-width="2"/></svg>Sicherheitsschloss</li>
    <li><svg viewBox="0 0 16 16"><path d="M1 6h3l4-4v12l-4-4H1z"/><path d="M11 5a4 4 0 010 6M13 3a7 7 0 010 10" fill="none" stroke="#5f9a56" stroke-width="1.5"/></svg>Alarmanlage</li>
    <li><svg viewBox="0 0 16 16"><path d="M8 1a5 5 0 013 9v2H5v-2A5 5 0 018 1z" fill="none" stroke="#5f9a56" stroke-width="1.6"/><rect x="5.5" y="13" width="5" height="2.5"/></svg>Licht</li>
  </ul>

  <footer class="imprint">
    <span>H.Lorenz GmbH</span><span class="dot">●</span>
    <span>Geschäftsführer: Herr Jonas Lorenz</span><span class="dot">●</span>
    <span>Werkstattweg 7</span><span class="dot">●</span>
    <span>50999 Köln</span>
    <span><svg viewBox="0 0 16 16"><circle cx="8" cy="4" r="4"/><path d="M1 16c0-5 3-7 7-7s7 2 7 7z"/></svg>02234 5550182</span>
    <span><svg viewBox="0 0 16 16"><rect x="0" y="2" width="16" height="12"/><path d="M0 2l8 6 8-6" fill="none" stroke="#fff" stroke-width="1.5"/></svg>jl@kistenhalle.de</span>
  </footer>
</section>

<!-- Seite B -->
<section class="flyer-side side-b">
  <header class="side-header">
    <div class="brand"><span class="brand-square"></span><span class="brand-name">Kistenhalle</span></div>
    <div class="web">www.kistenhalle.de</div>
    <ul class="claims">
      <li><svg><use href="#tick-white"/></svg>Günstig</li>
      <li><svg><use href="#tick-white"/></svg>Sicher</li>
      <li><svg><use href="#tick-white"/></svg>Lagern</li>
    </ul>
  </header>

  <h2 class="headline">KLEINER PREIS BEI TOP KONDITIONEN</h2>

  <div class="benefits">
    <article class="benefit">
      <h3><svg><use href="#tick-green"/></svg>Mehr Platz</h3>
      <p>Verschaffen Sie sich mehr Platz!<br>Ob privat (Umzug, fehlende Garage, voller Keller) oder gewerblich (zur Lagerung von Akten, Gerätepark, Warenlager) – nutzen Sie Lagercontainer zur Platzoptimierung.</p>
    </article>
    <article class="benefit">
      <h3><svg><use href="#tick-green"/></svg>Ebenerdig</h3>
      <p>Auf dem befestigten Gelände können Sie auch mit großen Fahrzeugen direkt an die Lagercontainer heranfahren und bequem be- oder entladen, ohne große Wege gehen zu müssen.</p>
    </article>
    <article class="benefit">
      <h3><svg><use href="#tick-green"/></svg>Rentabel</h3>
      <p>Nutzen Sie den Platz in Ihrer Wohnung oder Firma rentabler und lagern Sie die wichtigen, aber nicht täglich benötigten Dinge in einen günstigen Lagerraum aus.</p>
    </article>
  </div>

  <footer class="imprint">
    <span>H.Lorenz GmbH</span><span class="dot">●</span>
    <span>Geschäftsführer: Herr Jonas Lorenz</span><span class="dot">●</span>
    <span>Werkstattweg 7</span><span class="dot">●</span>
    <span>50999 Köln</span>
    <span><svg viewBox="0 0 16 16"><circle cx="8" cy="4" r="4"/><path d="M1 16c0-5 3-7 7-7s7 2 7 7z"/></svg>02234 5550182</span>
    <span><svg viewBox="0 0 16 16"><rect x="0" y="2" width="16" height="12"/><path d="M0 2l8 6 8-6" fill="none" stroke="#fff" stroke-width="1.5"/></svg>jl@kistenhalle.de</span>
  </footer>
</section>

</body>
</html>
```